Real Estate Website

I am looking for a website design for a website that will be featuring real estate listings across Australia. It will be a website for a real estate agency that operates through all states in Australia.

We like the designs of https://www.brightnest.com.au/ and https://valtoria.example/

On the brightnest website, we like the sell, buy, sold tabs but would also like lease, and agents. We also need a button somewhere for 'Join Agent Pivola' and 'Login'

On the Valtoria site it has a concierge section and we want something like that on the home page.

The contact details to show in the footer are:

Shop 2217B
Level 1 Harbourgate Shopping Centre
87 Quillon Terrace
Southport

Attached are various versions of the logo and some intro text to go on the home page.

```html
<!DOCTYPE html>
<html lang="en">
<head>
<meta charset="utf-8">
<title>Agent Pivola — Real Estate Across Australia</title>
<link rel="stylesheet" href="https://fonts.googleapis.com/css2?family=Montserrat:wght@300;400;500;600&family=Lato:wght@400;700&family=Poppins:wght@400;500;600&display=swap">
<style>
:root{
  --navy:#1c3550;
  --navy-deep:#13263b;
  --gold:#c59a45;
  --gold-light:#efe1a2;
  --gold-dark:#a97a35;
  --grey-bg:#f2f2f2;
  --cream:#f3efe9;
  --ink:#222;
  --muted:#666;
  --footer:#2b2b2b;
  --line:#e3e3e3;
  --white:#fff;
}
*{box-sizing:border-box;margin:0;padding:0}
html,body{width:1200px;height:4089px;overflow:hidden}
body{position:relative;font-family:"Lato",sans-serif;color:var(--ink);background:var(--white)}
.abs{position:absolute}
.btn-gold{position:absolute;display:flex;align-items:center;justify-content:center;gap:8px;color:var(--white);font-family:"Lato",sans-serif;font-weight:700;font-size:16px;background:linear-gradient(90deg,var(--gold-light),var(--gold-dark))}
.btn-gold .dot{width:15px;height:15px;border-radius:50%;background:var(--white);display:inline-block;position:relative}
.btn-gold .dot::after{content:"";position:absolute;left:5px;top:4px;border-left:5px solid var(--gold-dark);border-top:3.5px solid transparent;border-bottom:3.5px solid transparent}
.section-title{position:absolute;left:0;width:1200px;text-align:center;font-family:"Montserrat",sans-serif;font-weight:300;font-size:32px;color:var(--ink);letter-spacing:.5px}
.section-title b{font-weight:600}
.underline{position:absolute;left:560px;width:80px;height:3px;background:linear-gradient(90deg,var(--gold-light),var(--gold-dark))}

/* Hero */
.hero{position:absolute;left:0;top:0;width:1200px;height:600px;background:linear-gradient(180deg,#23435f 0%,#3a6b8d 35%,#6b8aa0 55%,#2c4a63 78%,#1b3246 100%)}
.brand{position:absolute;left:111px;top:54px;font-family:"Montserrat",sans-serif;font-weight:500;font-size:14px;letter-spacing:3px;color:var(--gold)}
.brand-mark{position:absolute;left:158px;top:10px;width:36px;height:36px;border:1.5px solid var(--gold);border-radius:50%}
.nav{position:absolute;top:44px;left:343px;display:flex;gap:32px;font-family:"Montserrat",sans-serif;font-weight:500;font-size:12.5px;color:var(--white)}
.nav .active{color:var(--gold-light)}
.nav-btn{position:absolute;top:29px;height:46px;border:2px solid var(--white);border-radius:4px;color:var(--white);font-family:"Montserrat",sans-serif;font-weight:600;font-size:14px;display:flex;align-items:center;justify-content:center}
.hero-title{position:absolute;left:0;width:1200px;top:215px;text-align:center;font-family:"Montserrat",sans-serif;font-weight:400;font-size:84px;letter-spacing:16px;color:var(--white)}
.arrow-circle{position:absolute;width:28px;height:28px;border:1.5px solid var(--white);border-radius:50%}
.arrow-circle svg{position:absolute;left:8px;top:7px}
.tabs{position:absolute;left:181px;top:335px;height:51px;display:flex;font-weight:700;font-size:16px;color:var(--white)}
.tabs span{display:flex;align-items:center;justify-content:center;background:rgba(150,160,170,.55)}
.tabs .on{background:rgba(140,165,175,.95)}
.search{position:absolute;left:181px;top:386px;width:665px;height:47px;background:var(--white);display:flex;align-items:center;padding-left:17px;font-size:16px;color:#555}
.estimate{left:846px;top:386px;width:208px;height:47px;font-size:15px}

/* Category strip */
.cat{position:absolute;top:652px;height:307px;display:flex;align-items:flex-end;justify-content:center;padding-bottom:18px;font-family:"Poppins",sans-serif;font-weight:600;font-size:20px;color:var(--white)}
.cat-arrow{position:absolute;top:780px;width:24px;height:24px;border:1.3px solid #333;border-radius:50%;background:rgba(255,255,255,.6)}
.cat-arrow svg{position:absolute;left:7px;top:6px}

/* Featured */
.featured{position:absolute;left:0;top:1043px;width:1200px;height:847px;background:var(--grey-bg)}
.lead{position:absolute;left:0;width:1200px;text-align:center;font-size:16px;color:#333}
.card{position:absolute;top:1262px;width:309px;height:425px;background:var(--white);box-shadow:0 2px 8px rgba(0,0,0,.08)}
.card .photo{height:182px}
.card .loc{position:absolute;left:18px;top:207px;font-size:14px;color:#444;display:flex;align-items:center;gap:8px}
.card .flag{width:28px;height:15px;background:#27356f}
.card h3{position:absolute;left:18px;top:244px;font-family:"Lato",sans-serif;font-weight:700;font-size:16.5px;color:#111}
.card .price{position:absolute;left:18px;top:279px;font-size:16px;color:#333}
.card .specs{position:absolute;left:20px;top:318px;width:270px;display:flex;justify-content:space-between;font-size:13px;color:#666}
.card .specs span{display:flex;align-items:center;gap:5px}
.card .specs i{display:inline-block;width:16px;height:11px;border:1.5px solid #888;border-radius:2px}
.card .rule{position:absolute;left:10px;right:10px;top:368px;height:1px;background:var(--line)}
.card .meta{position:absolute;left:23px;right:23px;top:385px;display:flex;justify-content:space-between;font-size:14px;color:#333}

/* About */
.about{position:absolute;left:0;top:1890px;width:1200px;height:600px;background:linear-gradient(90deg,#f1e6a6 0%,#dcc477 40%,#c49b50 75%,#b5883f 100%)}
.about-title{position:absolute;left:628px;top:1990px;font-family:"Poppins",sans-serif;font-weight:600;font-size:30px;color:var(--white)}
.about-text{position:absolute;left:628px;width:460px;font-size:14.5px;line-height:28px;color:var(--white)}
.btn-white{position:absolute;left:628px;top:2331px;width:150px;height:50px;background:var(--white);color:var(--gold);font-weight:700;font-size:16px;display:flex;align-items:center;justify-content:center;gap:8px}
.btn-white .dot{width:15px;height:15px;border-radius:50%;background:var(--gold);position:relative}
.btn-white .dot::after{content:"";position:absolute;left:5px;top:4px;border-left:5px solid var(--white);border-top:3.5px solid transparent;border-bottom:3.5px solid transparent}

/* Concierge */
.banner{position:absolute;left:111px;top:2676px;width:978px;height:344px;border-radius:12px;background:linear-gradient(180deg,#5a7386 0%,#8aa0ad 30%,#475a5f 60%,#1f4756 100%)}
.banner-q{position:absolute;left:150px;top:2752px;width:405px;text-align:center;font-family:"Poppins",sans-serif;font-weight:600;font-size:20px;line-height:34px;color:var(--white)}
.banner-p{position:absolute;left:615px;top:2752px;width:440px;text-align:center;font-size:14.5px;line-height:34px;color:var(--white)}

/* Contact */
.contact{position:absolute;left:0;top:3110px;width:1200px;height:532px;background:var(--cream)}
.field{position:absolute;height:50px;background:var(--white);border-radius:4px;box-shadow:0 1px 4px rgba(0,0,0,.08);font-size:14px;color:#555;padding:15px 17px}

/* Footer */
.footer{position:absolute;left:0;top:3642px;width:1200px;height:447px;background:var(--footer)}
.footer-brand{position:absolute;left:111px;top:3862px;width:254px;text-align:center;font-family:"Montserrat",sans-serif;font-weight:400;font-size:24px;letter-spacing:4px;color:var(--gold)}
.social{position:absolute;top:3916px;width:28px;height:28px;border-radius:50%;border:1.5px solid var(--gold)}
.social.on{background:var(--gold)}
.foot-h{position:absolute;top:3696px;font-family:"Poppins",sans-serif;font-weight:600;font-size:25px;color:var(--white)}
.foot-u{position:absolute;top:3740px;width:150px;height:2px;background:linear-gradient(90deg,var(--gold),#4a4030)}
.foot-list{position:absolute;top:3768px;list-style:none;font-family:"Poppins",sans-serif;font-size:15px;line-height:31px;color:var(--white)}
.contact-item{position:absolute;left:898px;width:300px;font-family:"Poppins",sans-serif;font-size:15.5px;line-height:26px;color:var(--white);white-space:nowrap}
.contact-icon{position:absolute;left:856px}
.foot-rule{position:absolute;left:111px;top:4026px;width:978px;height:1px;background:#555}
.copyright{position:absolute;left:0;width:1200px;top:4048px;text-align:center;font-family:"Poppins",sans-serif;font-size:15px;color:var(--white)}
</style>
</head>
<body>

<!-- Hero -->
<header class="hero" role="img" aria-label="Harbour city skyline with opera house at dusk"></header>
<div class="brand-mark"></div>
<div class="brand">AGENT PIVOLA</div>
<nav class="nav">
  <span class="active">HOME</span><span>SELL ▾</span><span>BUY ▾</span><span>CONCIERGE</span><span>LEASE</span><span>AGENTS</span>
</nav>
<div class="nav-btn" style="left:817px;width:170px">JOIN AGENT PIVOLA</div>
<div class="nav-btn" style="left:1006px;width:80px">LOGIN</div>
<h1 class="hero-title">AGENT PIVOLA</h1>
<div class="arrow-circle" style="left:38px;top:286px"><svg width="10" height="12"><path d="M7 1 L2 6 L7 11" stroke="#fff" stroke-width="1.6" fill="none"/></svg></div>
<div class="arrow-circle" style="left:1133px;top:286px"><svg width="10" height="12"><path d="M3 1 L8 6 L3 11" stroke="#fff" stroke-width="1.6" fill="none"/></svg></div>
<div class="tabs"><span class="on" style="width:82px">Sell</span><span style="width:70px">Buy</span><span style="width:75px">Sold</span></div>
<div class="search">Start typing to find your address</div>
<div class="btn-gold estimate">Get Property Estimate</div>

<!-- Category strip -->
<div class="cat" style="left:0;width:86px;background:linear-gradient(90deg,#d9d6d2,#ece9e5)" role="img" aria-label="Agent holding documents"></div>
<div class="cat" style="left:111px;width:309px;background:linear-gradient(180deg,#9fb3c4,#6e7466 60%,#4a5a3c)" role="img" aria-label="Two-storey family home at evening">SELL</div>
<div class="cat" style="left:446px;width:308px;background:linear-gradient(135deg,#8a8c90,#c9c3bb 55%,#6f6a65)" role="img" aria-label="Keys and small house model handed over">BUY</div>
<div class="cat" style="left:779px;width:310px;background:linear-gradient(180deg,#d8d2c8,#a48c70 60%,#5b3e2a)" role="img" aria-label="Bright interior with timber floors and staircase">SOLD</div>
<div class="cat" style="left:1119px;width:81px;background:linear-gradient(90deg,#eef0f2,#dfe3e6)" role="img" aria-label="White interior"></div>
<div class="cat-arrow" style="left:30px"><svg width="8" height="10"><path d="M6 1 L2 5 L6 9" stroke="#333" stroke-width="1.4" fill="none"/></svg></div>
<div class="cat-arrow" style="left:1149px"><svg width="8" height="10"><path d="M2 1 L6 5 L2 9" stroke="#333" stroke-width="1.4" fill="none"/></svg></div>

<!-- Featured listings -->
<section class="featured"></section>
<h2 class="section-title" style="top:1121px">FEATURED <b>LISTINGS</b></h2>
<div class="underline" style="top:1181px"></div>
<p class="lead" style="top:1207px">Lorem ipsum dolor sit amet, consectetur adipiscing elit, sed do eiusmod tempor magna aliqua.</p>

<article class="card" style="left:111px">
  <div class="photo" role="img" aria-label="Modern apartment block with lawn" style="background:linear-gradient(180deg,#5f8fc9,#3d4450 55%,#6f8b4a)"></div>
  <div class="loc"><span class="flag"></span>New South Wales &nbsp;›&nbsp; Victoria</div>
  <h3>Spacious One bedroom Apartment</h3>
  <div class="price">~ USD$ 69,000</div>
  <div class="specs"><span>4 <i></i></span><span>4 <i></i></span><span>1 <i></i></span><span>300 m² <i style="width:12px"></i></span></div>
  <div class="rule"></div>
  <div class="meta"><span>4 days ago</span><span>Apartmen</span></div>
</article>
<article class="card" style="left:446px">
  <div class="photo" role="img" aria-label="Open living room overlooking a pool" style="background:linear-gradient(180deg,#c9b79d,#8a6a52 50%,#5b8fa4)"></div>
  <div class="loc"><span class="flag"></span>New South Wales &nbsp;›&nbsp; Victoria</div>
  <h3>Spacious One bedroom Apartment</h3>
  <div class="price">~ USD$ 69,000</div>
  <div class="specs"><span>4 <i></i></span><span>4 <i></i></span><span>1 <i></i></span><span>300 m² <i style="width:12px"></i></span></div>
  <div class="rule"></div>
  <div class="meta"><span>4 days ago</span><span>Apartmen</span></div>
</article>
<article class="card" style="left:779px">
  <div class="photo" role="img" aria-label="Townhouses lit at dusk" style="background:linear-gradient(180deg,#a9b9c6,#6b5a45 55%,#44513a)"></div>
  <div class="loc"><span class="flag"></span>New South Wales &nbsp;›&nbsp; Victoria</div>
  <h3>Spacious One bedroom Apartment</h3>
  <div class="price">~ USD$ 69,000</div>
  <div class="specs"><span>4 <i></i></span><span>4 <i></i></span><span>1 <i></i></span><span>300 m² <i style="width:12px"></i></span></div>
  <div class="rule"></div>
  <div class="meta"><span>4 days ago</span><span>Apartmen</span></div>
</article>
<div class="btn-gold" style="left:525px;top:1742px;width:150px;height:51px">View More <span class="dot"></span></div>

<!-- About -->
<section class="about"></section>
<div class="abs" style="left:130px;top:1998px;width:375px;height:327px;background:linear-gradient(180deg,#8f9fc0,#d7a78d 35%,#4a4a45 60%,#3a6f9a)" role="img" aria-label="Luxury home with pool at sunset"></div>
<div class="abs" style="left:317px;top:2158px;width:254px;height:224px;background:linear-gradient(180deg,#d9b07c,#e8e2d8 45%,#7c8a95)" role="img" aria-label="White two-storey villa with pool"></div>
<h2 class="about-title">ABOUT US</h2>
<p class="about-text" style="top:2070px">Lorem ipsum dolor sit amet, consectetur adipiscing elit, sed do eiusmod tempor incididunt ut labore et dolore magna aliqua. Ut enim ad minim veniam, quis nostrud exercitation ullamco laboris nisi ut aliquip ex ea commodo consequat.</p>
<p class="about-text" style="top:2212px">Duis aute irure dolor in reprehenderit in voluptate velit esse cillum dolore eu fugiat nulla pariatur. Excepteur sint occaecat cupidatat non proident, sunt in culpa qui officia deserunt laborum.</p>
<div class="btn-white">View More <span class="dot"></span></div>

<!-- Concierge -->
<h2 class="section-title" style="top:2581px">AGENT PIVOLA <b>CONCIERGE</b></h2>
<div class="underline" style="top:2633px"></div>
<div class="banner" role="img" aria-label="Modern residence with infinity pool over a valley"></div>
<p class="banner-q">Looking buy, rent or sell something unique? Want competitive developer financing at great rates?</p>
<p class="banner-p">Agent Pivola can help you find, buy, rent or sell unique properties through our extensive global agent network and assist with financing at competitive rates with fast approvals.</p>
<div class="btn-gold" style="left:511px;top:2914px;width:178px;height:49px">Find Out More <span class="dot"></span></div>

<!-- Contact -->
<section class="contact"></section>
<h2 class="section-title" style="top:3183px">CONTACT <b>US</b></h2>
<div class="underline" style="top:3236px"></div>
<div class="field" style="left:183px;top:3277px;width:411px">Name</div>
<div class="field" style="left:606px;top:3277px;width:411px">Email</div>
<div class="field" style="left:183px;top:3340px;width:411px">Phone Number</div>
<div class="field" style="left:606px;top:3340px;width:411px">Subject</div>
<div class="field" style="left:183px;top:3403px;width:834px;height:86px">Message</div>
<div class="btn-gold" style="left:528px;top:3512px;width:139px;height:51px">SUBMIT</div>

<!-- Footer -->
<footer class="footer"></footer>
<div class="footer-brand">AGENT PIVOLA</div>
<div class="social on" style="left:165px"></div>
<div class="social" style="left:203px"></div>
<div class="social" style="left:241px"></div>
<div class="social" style="left:279px"></div>

<h3 class="foot-h" style="left:419px">Quick Links</h3>
<div class="foot-u" style="left:419px"></div>
<ul class="foot-list" style="left:419px"><li>Home</li><li>About Us</li><li>Services</li><li>Blog</li><li>Contact Us</li></ul>

<h3 class="foot-h" style="left:620px">Resources</h3>
<div class="foot-u" style="left:620px"></div>
<ul class="foot-list" style="left:620px"><li>Privacy Policy</li><li>Terms and Conditions</li><li>Terms of Use</li><li>Faq</li><li>Support</li></ul>

<h3 class="foot-h" style="left:847px">Contact Us</h3>
<div class="foot-u" style="left:847px"></div>
<svg class="contact-icon" style="top:3778px" width="26" height="26" viewBox="0 0 24 24"><path d="M6 3 L9 3 L10 8 L8 9.5 C9 12 11 14.5 14.5 16 L16 14 L21 15 L21 18 C21 19.5 19.5 21 18 21 C10 20 4 14 3 6 C3 4.5 4.5 3 6 3 Z" fill="none" stroke="var(--gold)" stroke-width="1.6"/></svg>
<div class="contact-item" style="top:3776px">Phone<br>+61 7 5550 1427</div>
<svg class="contact-icon" style="top:3844px" width="26" height="20" viewBox="0 0 26 20"><rect x="1" y="1" width="24" height="18" fill="none" stroke="var(--gold)" stroke-width="1.6"/><path d="M1 1 L13 11 L25 1" fill="none" stroke="var(--gold)" stroke-width="1.6"/></svg>
<div class="contact-item" style="top:3840px">Email<br>hello@agentpivola.example</div>
<svg class="contact-icon" style="top:3906px;left:858px" width="22" height="28" viewBox="0 0 22 28"><path d="M11 27 C4 18 2 14 2 10 A9 9 0 0 1 20 10 C20 14 18 18 11 27 Z" fill="var(--gold)"/><circle cx="11" cy="10" r="3.5" fill="var(--footer)"/></svg>
<div class="contact-item" style="top:3906px;font-size:14.5px;line-height:24px">Address<br>Shop 2217B, Level 1<br>Harbourgate Shopping Centre<br>87 Quillon Terrace, Southport</div>

<div class="foot-rule"></div>
<p class="copyright">Copyrights@2025. Agent Pivola.All Rights Reserved</p>

</body>
</html>
```